Business Card for a New Zealand IT Startup

I need a business card for VELTA Holdings. We are a young startup based in New Zealand working in internet marketing and web development. The design should have some element connected to New Zealand, such as wave, koru or silver fern, just don't use a kiwi bird.

```html
<!DOCTYPE html>
<html lang="en">
<head>
<meta charset="utf-8">
<title>VELTA Holdings – Business Card</title>
<link href="https://fonts.googleapis.com/css2?family=Source+Sans+3:wght@400;600;700&display=swap" rel="stylesheet">
<style>
  :root{
    --brand-blue:#0a6bb8;
    --brand-orange:#e8581e;
    --card-white:#ffffff;
    --text-grey:#3d3d3d;
    --page-bg:#e9eaec;
  }
  *{box-sizing:border-box;margin:0;padding:0}
  html,body{width:1200px;height:1000px;overflow:hidden}
  body{
    background:var(--page-bg);
    font-family:"Source Sans 3",Arial,sans-serif;
    position:relative;
  }
  .card{
    position:absolute;
    overflow:hidden;
    box-shadow:0 6px 18px rgba(0,0,0,.18);
  }
  /* back side */
  .card-back{
    left:430px;top:60px;width:620px;height:354px;
    background:var(--brand-blue);
    display:flex;flex-direction:column;align-items:center;justify-content:center;gap:18px;
  }
  .card-back .brand-dot{
    width:150px;height:150px;border-radius:50%;background:var(--card-white);
  }
  .card-back .brand-name{
    color:var(--card-white);font-weight:700;font-size:34px;letter-spacing:1px;
  }
  /* front side */
  .card-front{
    left:140px;top:450px;width:760px;height:434px;
    background:var(--card-white);
  }
  .card-front .accent{position:absolute;inset:0}
  .front-content{position:absolute;left:44px;top:38px}
  .brand-name-front{
    color:var(--brand-blue);font-weight:700;font-size:44px;line-height:1;letter-spacing:.5px;
  }
  .person-name{
    margin-top:34px;color:var(--brand-blue);font-weight:700;font-size:24px;line-height:1.1;
  }
  .person-title{
    color:var(--brand-orange);font-weight:400;font-size:17px;text-transform:uppercase;
  }
  .address{
    margin-top:12px;margin-left:20px;color:var(--text-grey);font-size:18px;line-height:1.2;
  }
  .contact-list{list-style:none;margin-top:10px;color:var(--text-grey);font-size:18px;line-height:1.25}
  .contact-list li{display:flex;align-items:center;gap:8px}
  .contact-list svg{width:15px;height:15px;fill:var(--brand-blue);flex:none}
</style>
</head>
<body>

<section class="card card-back" aria-label="Card back">
  <span class="brand-dot"></span>
  <span class="brand-name">VELTA Holdings</span>
</section>

<section class="card card-front" aria-label="Card front">
  <svg class="accent" viewBox="0 0 760 434" aria-hidden="true">
    <rect x="540" y="0" width="220" height="434" fill="var(--brand-orange)"/>
    <circle cx="560" cy="250" r="190" fill="var(--card-white)"/>
    <circle cx="540" cy="260" r="120" fill="var(--brand-blue)"/>
  </svg>

  <div class="front-content">
    <div class="brand-name-front">VELTA Holdings</div>
    <div class="person-name">MARA TANE</div>
    <div class="person-title">President</div>
    <div class="address">27 Harbour View Road<br>Devonport, Auckland 0624</div>
    <ul class="contact-list">
      <li><svg viewBox="0 0 16 16"><path d="M3 1l3 3-2 2c1 2 3 4 5 5l2-2 3 3-2 3C6 14 2 10 1 3z"/></svg>09 445 2190</li>
      <li><svg viewBox="0 0 16 16"><path d="M4 0h8v16H4zM5.5 2v10h5V2z"/></svg>021 738 4462</li>
      <li><svg viewBox="0 0 16 16"><path d="M4 1h8v4H4zM1 6h14v7h-3v2H4v-2H1zM5 11v3h6v-3z"/></svg>09 445 2191</li>
      <li><svg viewBox="0 0 16 16"><path d="M0 3h16v10H0zM1 4l7 5 7-5z" fill-rule="evenodd"/></svg>mara@veltaholdings.co.nz</li>
      <li><svg viewBox="0 0 16 16"><path d="M8 0a8 8 0 1 0 0 16A8 8 0 0 0 8 0zM8 3a3 3 0 0 1 3 3c0 2-3 6-3 6S5 8 5 6a3 3 0 0 1 3-3z" fill-rule="evenodd"/></svg>www.veltaholdings.co.nz</li>
    </ul>
  </div>
</section>

</body>
</html>
```